Talon Microsystems PowerPoint Master Slide Deck Design

This is a 2-phase project to design a slide deck for a semiconductor company in the Silicon Valley. The design budget will be increased with each phase.
The slide deck will need to have one version with a dark background for presentations and a second version with a white background. Otherwise, the slides will be the same. I anticipate we will need a total of 10 slides, but that number may change.
The first phase will be to design a Title and a Title and Content slide.
- The Title Slide is the first slide of the deck. It should include the presentation title, the presenter's name and date of presentation
- The Title and Content slide should include a title and content with bullet points and up to 2 additional sub-bullets
- The Title and Content slide should have a footer that includes the slide #, Talon Microsystems Confidential, and the logo. This footer will be on every slide except the Title Slide
The first two slides will serve as the format for the remaining ~8 slides:
-Header and Content Text (1, 2, 4 column)
-Header and Content Image (bar chart, pie chart, tables)
-Break
-Title only
-Closing (Talon logo only)
Our slides contain a lot of content so a clean and simple design is best.
Both phases will need to include pre-set color options for
-Text and Lines
-Shadows
-Bullets and sub-bullets (including shapes, ex. circle, slash, square, etc.)
-Bar charts, pie charts, tables
Samples of our collateral are attached. Logo files are also attached
Look and feel
Each slider illustrates characteristics of the customer's brand and the style your logo design should communicate.

```html
<!DOCTYPE html>
<html lang="en">
<head>
<meta charset="utf-8">
<title>Talon Microsystems Slide Master</title>
<link href="https://fonts.googleapis.com/css2?family=Mulish:wght@400;600;700;800;900&display=swap" rel="stylesheet">
<style>
:root{
  --page:#1b1b1b;
  --blue:#1d43e8;
  --sky:#29a8e0;
  --ink:#2b2b2b;
  --body:#555a60;
  --panel:#e6eef7;
  --subpanel:#d3e0ec;
  --white:#ffffff;
}
*{margin:0;padding:0;box-sizing:border-box}
html,body{width:1200px;height:3812px;overflow:hidden;background:var(--page);font-family:'Mulish',sans-serif}
.slide{position:absolute;left:91px;width:1002px;height:564px;background:var(--white);overflow:hidden}
.brand{position:absolute;left:18px;top:20px;width:215px;display:flex;align-items:center;gap:12px;font-weight:800;font-size:24px;line-height:27px;color:var(--blue);letter-spacing:.3px}
.brand .dot{flex:none;width:16px;height:16px;border-radius:50%;background:var(--blue)}
.slide-title{position:absolute;top:28px;font-size:40px;line-height:48px;font-weight:900;color:var(--blue);letter-spacing:.5px}
.footer{position:absolute;left:0;right:0;bottom:0;height:39px;background:var(--sky);color:var(--white);font-size:13px;display:flex;align-items:center;padding:0 22px 0 14px}
.footer .fdot{width:12px;height:12px;border-radius:50%;background:var(--white);margin-right:22px}
.footer .num{margin-left:auto}

/* title slide */
.title-slide .bg{position:absolute;inset:0;background:radial-gradient(ellipse at 30% 40%,#c9dbe8 0%,#dce7ee 45%,#e8eef2 100%)}
.title-slide .brand-r{position:absolute;right:60px;top:52px;display:flex;align-items:center;gap:10px;font-weight:800;font-size:30px;color:var(--blue)}
.title-slide .brand-r .dot{width:16px;height:16px;border-radius:50%;background:var(--blue)}
.meta{position:absolute;right:68px;top:183px;text-align:right;color:var(--ink);font-size:24px;line-height:37px}
.meta .name{color:var(--blue);font-weight:800;font-size:32px}
.welcome{position:absolute;left:610px;width:400px;top:343px;text-align:center;color:var(--blue);font-weight:900;line-height:1}
.welcome .w1{font-size:38px}
.welcome .w2{font-size:80px;margin-top:10px}
.welcome .w3{font-size:31px;margin-top:12px}

/* about */
.about-photo{position:absolute;left:0;top:100px;width:522px;height:425px;background:linear-gradient(135deg,#3c2d8f,#6a5ad8 45%,#2a2466)}
.about-strip{position:absolute;left:522px;top:495px;width:105px;height:30px;background:#2a2466}
.about-text{position:absolute;left:567px;top:140px;width:375px}
.about-text h3{font-size:19px;font-weight:800;color:var(--ink);line-height:24px;margin-bottom:20px}
.about-text p{font-size:13.5px;line-height:18.8px;color:var(--body)}

/* solutions */
.sol-panel{position:absolute;top:117px;width:464px;height:408px;background:var(--panel);padding:30px 32px}
.sol-panel h3{font-size:17px;font-weight:800;color:var(--ink);line-height:24px;margin-bottom:14px}
.sol-list{list-style:none}
.sol-list li{position:relative;padding-left:18px;font-size:13.5px;color:var(--ink);line-height:27px}
.sol-list li::before{content:"";position:absolute;left:1px;top:9px;border-left:6px solid var(--blue);border-top:4.5px solid transparent;border-bottom:4.5px solid transparent}
.sub-list{list-style:none;background:var(--subpanel);margin:3px 0 6px 22px;width:330px;padding:5px 0 7px 32px}
.sub-list li{position:relative;font-size:13.5px;color:var(--ink);line-height:21px}
.sub-list li::before{content:"";position:absolute;left:-20px;top:7px;width:8px;height:8px;border-radius:50%;background:var(--blue)}

/* services */
.divider{position:absolute;left:250px;top:18px;width:3px;height:64px;background:var(--ink)}
.card{position:absolute;top:129px;width:292px;height:395px;background:var(--white);box-shadow:0 0 14px rgba(0,0,0,.08);text-align:center}
.card .icon{width:80px;height:80px;border-radius:50%;background:var(--blue);margin:34px auto 0;display:flex;align-items:center;justify-content:center}
.card h4{font-size:17px;font-weight:800;color:var(--ink);margin-top:28px}
.card p{font-size:12.5px;line-height:18px;color:var(--body);padding:0 40px;margin-top:16px}

/* break */
.break-slide .bg{position:absolute;inset:0;background:radial-gradient(ellipse at 50% 55%,#c4d0d9 0%,#d9e0e6 45%,#e3e8ec 100%)}
.break-title{position:absolute;left:0;right:0;top:196px;text-align:center;font-size:80px;line-height:90px;font-weight:900;color:var(--blue);letter-spacing:1px}
.break-sub{position:absolute;left:0;right:0;top:292px;text-align:center;font-size:16px;color:var(--ink)}

/* closing */
.closing-slide .bg{position:absolute;inset:0;background:linear-gradient(160deg,#9fd3f4 0%,#2f8ff0 40%,#1646ec 75%,#27a3f4 100%)}
.closing-brand{position:absolute;left:0;right:0;top:240px;display:flex;justify-content:center;align-items:center;gap:16px;font-size:60px;font-weight:800;color:var(--white)}
.closing-brand .dot{width:26px;height:26px;border-radius:50%;background:var(--white)}
</style>
</head>
<body>

<section class="slide title-slide" style="top:81px">
  <div class="bg" role="img" aria-label="Soft-focus circuit board photograph in pale blue-grey tones"></div>
  <div class="brand-r"><span class="dot"></span>Talon Microsystems</div>
  <div class="meta"><div class="name">Marcus</div><div>Presenter</div><div>14/12/2023</div></div>
  <div class="welcome"><div class="w1">WELCOME TO</div><div class="w2">TALON</div><div class="w3">MICROSYSTEMS</div></div>
</section>

<section class="slide" style="top:691px">
  <div class="brand"><span class="dot"></span><span>Talon<br>Microsystems</span></div>
  <h2 class="slide-title" style="left:281px">ABOUT US</h2>
  <div class="about-photo" role="img" aria-label="Gloved hand holding a processor chip over a purple-lit motherboard"></div>
  <div class="about-strip"></div>
  <div class="about-text">
    <h3>Lorem ipsum dolor sit amet consectetur adipiscing</h3>
    <p>Sed ut perspiciatis unde omnis iste natus error sit voluptatem accusantium doloremque laudantium, totam rem aperiam, eaque ipsa quae ab illo inventore veritatis et quasi architecto beatae vitae dicta sunt explicabo. Nemo enim ipsam voluptatem quia voluptas sit aspernatur aut odit aut fugit, sed quia consequuntur magni dolores eos qui ratione voluptatem sequi nesciunt. Neque porro quisquam est, qui dolorem ipsum quia dolor sit amet, consectetur, adipisci velit, sed quia non numquam eius modi tempora incidunt ut labore et dolore magnam aliquam quaerat voluptatem. Ut enim ad minima veniam, quis nostrum exercitationem ullam corporis suscipit laboriosam, nisi ut aliquid</p>
  </div>
  <footer class="footer"><span class="fdot"></span>Talon Microsystems Confidential<span class="num">2</span></footer>
</section>

<section class="slide" style="top:1292px">
  <div class="brand"><span class="dot"></span><span>Talon<br>Microsystems</span></div>
  <h2 class="slide-title" style="left:281px">SOLUTIONS</h2>
  <div class="sol-panel" style="left:19px">
    <h3>LOREM IPSUM DOLOR SIT AMET<br>CONSECTETUR ADIPISCING</h3>
    <ul class="sol-list">
      <li>Lorem ipsum dolor sit amet, consectetur adipiscing elit.</li>
      <li>In et urna nec enim facilisis fermentum.</li>
      <li>Nunc ornare libero at odio congue, eget malesuada</li>
    </ul>
    <ul class="sub-list">
      <li>Nullam auctor ex eu lobortis pretium.</li>
      <li>Nullam sit amet magna condimentum</li>
      <li>Integer a ex malesuada.</li>
    </ul>
    <ul class="sol-list">
      <li>Nunc malesuada sapien non justo tristique, quis tem</li>
      <li>Suspendisse tincidunt enim eget eros congue varius.</li>
      <li>Quisque id enim sagittis, suscipit magna quis, mattis ante.</li>
      <li>Aenean ultrices dui sollicitudin varius cursus.</li>
      <li>In efficitur nulla at mi rutrum lobortis vel eget sem.</li>
    </ul>
  </div>
  <div class="sol-panel" style="left:511px">
    <h3>LOREM IPSUM DOLOR SIT AMET<br>CONSECTETUR ADIPISCING</h3>
    <ul class="sol-list">
      <li>Lorem ipsum dolor sit amet, consectetur adipiscing elit.</li>
      <li>In et urna nec enim facilisis fermentum.</li>
      <li>Nunc ornare libero at odio congue, eget malesuada</li>
    </ul>
    <ul class="sub-list">
      <li>Nullam auctor ex eu lobortis pretium.</li>
      <li>Nullam sit amet magna condimentum</li>
      <li>Integer a ex malesuada.</li>
    </ul>
    <ul class="sol-list">
      <li>Nunc malesuada sapien non justo tristique, quis tem</li>
      <li>Suspendisse tincidunt enim eget eros congue varius.</li>
      <li>Quisque id enim sagittis, suscipit magna quis, mattis ante.</li>
      <li>Aenean ultrices dui sollicitudin varius cursus.</li>
      <li>In efficitur nulla at mi rutrum lobortis vel eget sem.</li>
    </ul>
  </div>
  <footer class="footer"><span class="fdot"></span>Talon Microsystems Confidential<span class="num">3</span></footer>
</section>

<section class="slide" style="top:1893px">
  <div class="brand"><span class="dot"></span><span>Talon<br>Microsystems</span></div>
  <div class="divider"></div>
  <h2 class="slide-title" style="left:274px">SERVICES</h2>
  <div class="card" style="left:37px">
    <div class="icon"><svg width="44" height="44" viewBox="0 0 44 44" fill="none" stroke="#fff" stroke-width="3"><rect x="10" y="10" width="24" height="24" rx="2"/><rect x="17" y="17" width="10" height="10"/><path d="M16 4v6M22 4v6M28 4v6M16 34v6M22 34v6M28 34v6M4 16h6M4 22h6M4 28h6M34 16h6M34 22h6M34 28h6"/></svg></div>
    <h4>LOREM IPSUM</h4>
    <p>Lorem ipsum dolor sit amet, consectetur adipiscing elit, sed do eiusmod tempor incididunt ut labore et dolore magna aliqua. Ut enim ad minim veniam, quis nostrud exerci tation ullamco laboris nisi ut aliquip ex ea commodo consequat. Duis aute irure dolor in reprehenderit in voluptate velit esse cillum dolore eu fugiat nulla pariatur</p>
  </div>
  <div class="card" style="left:357px">
    <div class="icon"><svg width="44" height="44" viewBox="0 0 44 44" fill="none" stroke="#fff" stroke-width="3"><circle cx="22" cy="22" r="7"/><path d="M22 5v6M22 33v6M5 22h6M33 22h6M10 10l4 4M30 30l4 4M34 10l-4 4M14 30l-4 4"/><circle cx="22" cy="22" r="13"/></svg></div>
    <h4>LOREM IPSUM</h4>
    <p>Lorem ipsum dolor sit amet, consectetur adipiscing elit, sed do eiusmod tempor incididunt ut labore et dolore magna aliqua. Ut enim ad minim veniam, quis nostrud exerci tation ullamco laboris nisi ut aliquip ex ea commodo consequat. Duis aute irure dolor in reprehenderit in voluptate velit esse cillum dolore eu fugiat nulla pariatur</p>
  </div>
  <div class="card" style="left:677px">
    <div class="icon"><svg width="44" height="44" viewBox="0 0 44 44" fill="none" stroke="#fff" stroke-width="3"><path d="M10 5h18l7 7v27H10z"/><path d="M16 18h13M16 24h13M16 30h8"/></svg></div>
    <h4>LOREM IPSUM</h4>
    <p>Lorem ipsum dolor sit amet, consectetur adipiscing elit, sed do eiusmod tempor incididunt ut labore et dolore magna aliqua. Ut enim ad minim veniam, quis nostrud exerci tation ullamco laboris nisi ut aliquip ex ea commodo consequat. Duis aute irure dolor in reprehenderit in voluptate velit esse cillum dolore eu fugiat nulla pariatur</p>
  </div>
  <footer class="footer"><span class="fdot"></span>Talon Microsystems Confidential<span class="num">4</span></footer>
</section>

<section class="slide break-slide" style="top:2502px">
  <div class="bg" role="img" aria-label="Faded close-up of a glowing microchip on a circuit board"></div>
  <div class="brand"><span class="dot"></span><span>Talon<br>Microsystems</span></div>
  <h2 class="break-title">HOW IT WORKS</h2>
  <p class="break-sub">Lorem ipsum dolor sit amet, consectetur adipiscing elit, sed do eiusmod tempor incidi</p>
  <footer class="footer"><span class="fdot"></span>Talon Microsystems Confidential<span class="num">5</span></footer>
</section>

<section class="slide closing-slide" style="top:3124px">
  <div class="bg" role="img" aria-label="Blue-tinted close-up of a silicon wafer grid"></div>
  <div class="closing-brand"><span class="dot"></span>Talon Microsystems</div>
</section>

</body>
</html>
```